Web Design for company in the healthcare industry

We need a web design for a new company in the healthcare industry (telehealth) which allows patients to schedule appointments at their convenience, view and monitor their results, and consult with specialists that fit their requirements. The aim is to help patients take charge of their own health.

We already have a logo (attached) and are working with a developer who will do all the back end programming once the design is ready. Apart from the colours in the logo, we think shades of gray would work well.

Target Market(s)

I imagine the vast majority would be professionals from 30-50 years old.

Industry/Entity Type

Health And Wellness

Number of Pages Required

4 page

Requirements
Must have
• Hand-sketched graphics, particularly on landing page.
Should not have
• We don't want any photographs of people

```html
<!DOCTYPE html>
<html lang="en">
<head>
<meta charset="utf-8">
<title>Medora – Telehealth</title>
<link href="https://fonts.googleapis.com/css2?family=Open+Sans:wght@400;600;700&family=Dancing+Script:wght@600&display=swap" rel="stylesheet">
<style>
  :root {
    --green: #8cc63f;
    --green-dark: #76ad2c;
    --green-ring: #cfe8ad;
    --blue: #1e73b4;
    --ink: #333333;
    --muted: #777777;
    --line: #d6d6d6;
    --band: #efefef;
    --footer: #2a2a2a;
    --white: #ffffff;
    --chalk-dark: #1e1e1e;
    --chalk-mid: #4a4a4a;
    --heart-red: #c8212a;
  }
  * { box-sizing: border-box; margin: 0; padding: 0; }
  html, body { width: 724px; height: 1200px; overflow: hidden; }
  body { font-family: "Open Sans", Arial, sans-serif; color: var(--ink); background: var(--white); }

  .site-header { height: 54px; display: flex; align-items: center; justify-content: space-between; padding: 0 34px 0 22px; }
  .brand { display: flex; align-items: center; gap: 7px; font-size: 21px; font-weight: 700; color: var(--blue); }
  .brand-dot { width: 14px; height: 14px; border-radius: 50%; background: var(--blue); }
  .main-nav { display: flex; gap: 36px; }
  .main-nav a { font-size: 9px; font-weight: 600; letter-spacing: .6px; color: var(--ink); text-decoration: none; }

  .hero { position: relative; height: 334px; }
  .hero-art {
    position: absolute; inset: 0;
    background:
      radial-gradient(ellipse 150px 120px at 52% 58%, rgba(200,33,42,.85), rgba(200,33,42,.35) 55%, rgba(200,33,42,0) 100%),
      radial-gradient(ellipse 520px 260px at 50% 40%, var(--chalk-mid), var(--chalk-dark));
  }
  .hero-banner { position: absolute; left: 0; top: 118px; width: 262px; height: 78px; background: var(--green); color: var(--white); padding: 10px 0 0 22px; }
  .hero-banner h1 { font-size: 28px; font-weight: 400; letter-spacing: 2px; line-height: 1.1; }
  .hero-banner p { font-family: "Dancing Script", cursive; font-size: 21px; line-height: 1.1; }
  .hero-dots { position: absolute; left: 22px; top: 210px; display: flex; gap: 6px; }
  .hero-dots span { width: 7px; height: 7px; border-radius: 50%; background: #999; }
  .hero-dots span:first-child { background: var(--white); }

  .steps { height: 192px; background: var(--green); display: flex; justify-content: center; padding-top: 22px; }
  .step { width: 150px; text-align: center; color: var(--white); }
  .step-icon {
    width: 84px; height: 84px; border-radius: 50%; margin: 0 auto 14px;
    border: 4px solid var(--green-ring);
    background: radial-gradient(circle at 50% 45%, #e4e4e4 0 28%, #f4f4f4 45%, var(--white) 70%);
  }
  .step-label { font-size: 9.5px; font-weight: 600; letter-spacing: .8px; line-height: 1.45; padding: 0 8px; }
  .step-arrow { width: 24px; padding-top: 12px; }

  .welcome { height: 170px; text-align: center; padding: 30px 36px 0; }
  .section-title { font-size: 19px; font-weight: 600; letter-spacing: 1.5px; color: var(--blue); margin-bottom: 14px; }
  .welcome p { font-size: 8.5px; line-height: 1.65; color: var(--muted); margin-bottom: 12px; }
  .btn { display: inline-block; background: var(--blue); color: var(--white); font-size: 8px; font-weight: 700; letter-spacing: 1px; padding: 6px 14px; border: 0; font-family: inherit; text-decoration: none; }

  .events { height: 170px; background: var(--band); padding: 22px 40px 0; }
  .events .section-title { text-align: center; margin-bottom: 20px; color: var(--ink); }
  .event-list { display: flex; gap: 40px; }
  .event { flex: 1; display: flex; gap: 12px; }
  .event-date { width: 50px; flex: none; text-align: center; color: var(--green-dark); border-right: 2px solid var(--green); padding-right: 8px; }
  .event-date strong { display: block; font-size: 22px; font-weight: 600; line-height: 1.1; }
  .event-date span { display: block; font-size: 7px; font-weight: 600; color: var(--ink); white-space: nowrap; }
  .event p { font-size: 8.5px; line-height: 1.6; color: var(--muted); margin-bottom: 6px; }
  .event a { font-size: 7.5px; font-weight: 700; color: var(--green-dark); text-decoration: none; letter-spacing: .6px; }

  .contact { height: 205px; text-align: center; padding-top: 24px; }
  .contact .section-title { margin-bottom: 18px; }
  .contact-form { width: 460px; margin: 0 auto; }
  .field-row { display: flex; gap: 14px; margin-bottom: 10px; }
  .field { flex: 1; height: 24px; border: 1px solid var(--line); display: flex; align-items: center; gap: 5px; padding: 0 8px; font-size: 8px; color: #999; text-align: left; }
  .field svg { flex: none; }
  .field.message { height: 42px; align-items: flex-start; padding-top: 7px; }
  .contact .btn { margin-top: 6px; padding: 7px 30px; }

  .site-footer { height: 75px; background: var(--footer); color: #bbb; display: flex; justify-content: space-between; padding: 16px 30px 0; }
  .social { display: flex; gap: 6px; margin-bottom: 10px; }
  .social span { width: 16px; height: 16px; border-radius: 50%; background: #555; }
  .copyright { font-size: 7.5px; }
  .footer-contact { display: flex; gap: 16px; }
  .footer-contact h2 { font-size: 12px; font-weight: 600; letter-spacing: 1px; color: var(--white); }
  .footer-contact ul { list-style: none; font-size: 7.5px; line-height: 1.6; }
  .footer-contact li { display: flex; gap: 5px; align-items: flex-start; margin-bottom: 4px; }
</style>
</head>
<body>
  <header class="site-header">
    <div class="brand"><span class="brand-dot"></span>Medora</div>
    <nav class="main-nav">
      <a href="#">HEALTH PACKAGES</a>
      <a href="#">APPOINTMENTS</a>
      <a href="#">SPECIALISTS</a>
    </nav>
  </header>

  <section class="hero">
    <div class="hero-art" role="img" aria-label="Hand-sketched chalkboard drawing of a barbell with a large red heart in the centre"></div>
    <div class="hero-banner">
      <h1>CARDIOLOGY</h1>
      <p>with a difference</p>
    </div>
    <div class="hero-dots"><span></span><span></span><span></span><span></span></div>
  </section>

  <section class="steps">
    <div class="step">
      <div class="step-icon" role="img" aria-label="Hand-sketched icon of hands holding a package"></div>
      <p class="step-label">1. SELECT A PACKAGE</p>
    </div>
    <svg class="step-arrow" width="24" height="60" viewBox="0 0 24 60"><path d="M8 20 L16 30 L8 40" fill="none" stroke="#ffffff" stroke-width="1.5"/></svg>
    <div class="step">
      <div class="step-icon" role="img" aria-label="Hand-sketched icon of a calendar with a pen"></div>
      <p class="step-label">2. SCHEDULE AN APPOINTMENT AT YOUR CONVENIENCE</p>
    </div>
    <svg class="step-arrow" width="24" height="60" viewBox="0 0 24 60"><path d="M8 20 L16 30 L8 40" fill="none" stroke="#ffffff" stroke-width="1.5"/></svg>
    <div class="step">
      <div class="step-icon" role="img" aria-label="Hand-sketched icon of a results document"></div>
      <p class="step-label">3. GET YOUR RESULT BACK</p>
    </div>
    <svg class="step-arrow" width="24" height="60" viewBox="0 0 24 60"><path d="M8 20 L16 30 L8 40" fill="none" stroke="#ffffff" stroke-width="1.5"/></svg>
    <div class="step">
      <div class="step-icon" role="img" aria-label="Hand-sketched icon of a cheerful heart"></div>
      <p class="step-label">4. A HEALTHIER YOU</p>
    </div>
  </section>

  <section class="welcome">
    <h2 class="section-title">WELCOME TO OUR SITE</h2>
    <p>Our care team brings trusted specialists to you wherever you are. Book visits when it suits you, follow your results online and choose the doctor who fits your needs. Taking charge of your health has never been this simple and clear. Start today with a package that suits you.</p>
    <a class="btn" href="#">READ MORE</a>
  </section>

  <section class="events">
    <h2 class="section-title">UPCOMING EVENTS</h2>
    <div class="event-list">
      <article class="event">
        <div class="event-date"><strong>23</strong><span>SEPT 2015</span></div>
        <div>
          <p>Free heart health screening day with our cardiology team. Short talks, simple checks and advice for busy professionals.</p>
          <a href="#">READ MORE</a>
        </div>
      </article>
      <article class="event">
        <div class="event-date"><strong>25</strong><span>SEPT 2015</span></div>
        <div>
          <p>Online session on managing blood pressure at work, hosted live by our specialists with open questions at the end.</p>
          <a href="#">READ MORE</a>
        </div>
      </article>
    </div>
  </section>

  <section class="contact">
    <h2 class="section-title">QUICK CONTACT</h2>
    <form class="contact-form">
      <div class="field-row">
        <div class="field"><svg width="8" height="8" viewBox="0 0 8 8"><circle cx="4" cy="2.5" r="2" fill="#aaa"/><path d="M0 8 Q4 3 8 8Z" fill="#aaa"/></svg>Enter Name</div>
        <div class="field"><svg width="9" height="7" viewBox="0 0 9 7"><rect x=".5" y=".5" width="8" height="6" fill="none" stroke="#aaa"/><path d="M.5 .5 L4.5 4 L8.5 .5" fill="none" stroke="#aaa"/></svg>Enter Email</div>
        <div class="field"><svg width="6" height="9" viewBox="0 0 6 9"><rect x=".5" y=".5" width="5" height="8" rx="1" fill="none" stroke="#aaa"/></svg>Enter Phone</div>
      </div>
      <div class="field-row">
        <div class="field message"><svg width="8" height="8" viewBox="0 0 8 8"><path d="M1 7 L1 5 L5 1 L7 3 L3 7Z" fill="none" stroke="#aaa"/></svg>Leave Message</div>
      </div>
      <button class="btn" type="button">SUBMIT</button>
    </form>
  </section>

  <footer class="site-footer">
    <div>
      <div class="social"><span></span><span></span><span></span><span></span></div>
      <p class="copyright">Copyright © 2015, Medora All Rights Reserved</p>
    </div>
    <div class="footer-contact">
      <h2>CONTACT US</h2>
      <ul>
        <li><svg width="7" height="10" viewBox="0 0 7 10"><path d="M3.5 10 L0.5 4.5 A3 3 0 1 1 6.5 4.5Z" fill="#bbb"/></svg>14 Harbour Lane,<br>Westfield</li>
        <li><svg width="8" height="8" viewBox="0 0 8 8"><path d="M1 1 L3 1 L4 3 L3 4 Q4 5.5 4.5 5 L5 4 L7 5 L7 7 Q3 8 1 1Z" fill="#bbb"/></svg>Phone: 1800 555 014</li>
      </ul>
    </div>
  </footer>
</body>
</html>
```